Brellwick Partners, LLC Stationary

Brellwick Partners, LLC is a new financial planning and consulting company. We are looking for designs on business cards, letterhead, envelopes, and anything else that would be useful. Our preference for business card design is two sided. We are looking for a professional and clean look with incorporating the logo and patriotic feel. Thank you to all who participate and good luck!

```html
<!DOCTYPE html>
<html lang="en">
<head>
<meta charset="utf-8">
<title>Brellwick Partners, LLC – Business Card</title>
<link href="https://fonts.googleapis.com/css2?family=Arimo:wght@400;600;700&display=swap" rel="stylesheet">
<style>
  :root {
    --navy: #1f3f66;
    --navy-deep: #173352;
    --red: #d9434b;
    --ink: #3a3f47;
    --paper: #ffffff;
    --stage: #eceef1;
  }
  * { box-sizing: border-box; margin: 0; padding: 0; }
  html, body { width: 1200px; height: 950px; overflow: hidden; }
  body {
    background: var(--stage);
    font-family: "Arimo", Arial, sans-serif;
    display: flex;
    flex-direction: column;
    align-items: center;
    justify-content: center;
    gap: 50px;
  }
  .card {
    position: relative;
    width: 700px;
    height: 400px;
    border-radius: 4px;
    overflow: hidden;
    box-shadow: 0 6px 20px rgba(0,0,0,0.18);
  }
  /* Back */
  .card-back {
    background: linear-gradient(120deg, var(--navy) 0%, var(--navy-deep) 100%);
    display: flex;
    align-items: center;
    justify-content: center;
  }
  .back-name {
    display: flex;
    align-items: center;
    gap: 16px;
    color: var(--paper);
    font-weight: 600;
    font-size: 38px;
    letter-spacing: 2px;
    text-transform: uppercase;
  }
  .back-name .dot {
    width: 22px; height: 22px; border-radius: 50%; background: var(--paper);
  }
  .back-web {
    position: absolute;
    left: 0; right: 0; bottom: 40px;
    text-align: center;
    color: var(--paper);
    font-size: 20px;
    letter-spacing: 2px;
  }
  /* Front */
  .card-front { background: var(--paper); }
  .front-swoosh { position: absolute; inset: 0; }
  .brand {
    position: absolute;
    left: 46px; top: 50px;
    display: flex; align-items: center; gap: 12px;
    color: var(--navy);
    font-weight: 600;
    font-size: 25px;
    letter-spacing: 1px;
    text-transform: uppercase;
  }
  .brand .dot { width: 18px; height: 18px; border-radius: 50%; background: var(--navy); }
  .address {
    position: absolute;
    left: 46px; top: 140px;
    color: var(--ink);
    font-size: 19px;
    line-height: 26px;
  }
  .contacts {
    position: absolute;
    left: 46px; top: 200px;
    list-style: none;
    color: var(--ink);
    font-size: 19px;
  }
  .contacts li { display: flex; align-items: center; gap: 10px; height: 27px; }
  .contacts svg { width: 16px; height: 16px; fill: var(--navy); flex: none; }
  .person {
    position: absolute;
    left: 396px; top: 290px;
    text-transform: uppercase;
  }
  .person-name { color: var(--navy); font-size: 24px; font-weight: 600; letter-spacing: 1px; }
  .person-title { color: var(--red); font-size: 18px; letter-spacing: 1px; margin-top: 4px; }
</style>
</head>
<body>
  <section class="card card-back">
    <div class="back-name"><span class="dot"></span>Brellwick Partners, LLC</div>
    <div class="back-web">www.brellwick.com</div>
  </section>

  <section class="card card-front">
    <svg class="front-swoosh" viewBox="0 0 700 400" aria-hidden="true">
      <path d="M360 0 H700 V400 H560 C630 260 590 90 360 0 Z" fill="var(--red)"/>
      <path d="M440 0 H700 V400 H600 C660 260 640 100 440 0 Z" fill="var(--navy)" stroke="var(--paper)" stroke-width="6"/>
    </svg>

    <div class="brand"><span class="dot"></span>Brellwick Partners, LLC</div>

    <address class="address" style="font-style:normal">
      2710 Harrowgate Lane<br>Marlow Heights, NY 11920
    </address>

    <ul class="contacts">
      <li>
        <svg viewBox="0 0 16 16"><path d="M3 1 L6 1 L7 5 L5 6 C6 8 8 10 10 11 L11 9 L15 10 L15 13 C15 14 14 15 13 15 C6 15 1 10 1 3 C1 2 2 1 3 1 Z"/></svg>
        555 0142 7781
      </li>
      <li>
        <svg viewBox="0 0 16 16"><rect x="2" y="5" width="12" height="9" rx="1"/><rect x="4" y="1" width="8" height="5" fill="var(--paper)" stroke="var(--navy)" stroke-width="1.2"/></svg>
        555 0199 3604
      </li>
      <li>
        <svg viewBox="0 0 16 16"><rect x="1" y="3" width="14" height="10" rx="1"/><path d="M1.5 4 L8 9 L14.5 4" fill="none" stroke="var(--paper)" stroke-width="1.3"/></svg>
        ellis@brellwick.com
      </li>
      <li>
        <svg viewBox="0 0 16 16"><circle cx="8" cy="8" r="7"/><path d="M1 8 H15 M8 1 C4 5 4 11 8 15 M8 1 C12 5 12 11 8 15" fill="none" stroke="var(--paper)" stroke-width="1"/></svg>
        www.brellwick.com
      </li>
    </ul>

    <div class="person">
      <div class="person-name">Ellis Marren</div>
      <div class="person-title">President</div>
    </div>
  </section>
</body>
</html>
```